Veranix - Solution provider in business consulting

Veranix is a swiss based company providing solutions for developing markets. The business covers various fields of business consulting, such as supply chain, product costs, quality management and manufacturing management. The Business operates in a efficient, straight and solution oriented manner.
The final design should communicate these characteristics. Asian people as well as as western people shall identify the qualities of the company at first sight.
The customer needs business cards with a simple view but an recognizable design, printed in high quality. Engraved elements such as the globe or simple words are possible.
Available colors are: (RAL)
102/102/102
51/102/102
153/204/153
255/102/51
Font: Calibri

```html
<!DOCTYPE html>
<html lang="en">
<head>
<meta charset="utf-8">
<title>Veranix – Business Card</title>
<link rel="stylesheet" href="https://fonts.googleapis.com/css2?family=Carlito:wght@400;700&display=swap">
<style>
  :root {
    --paper: #ffffff;
    --card-dark: #444444;
    --card-light: #bfbfbf;
    --brand-grey: #666666;
    --text-light: #ffffff;
    --crop-line: #000000;
  }
  * { margin: 0; padding: 0; box-sizing: border-box; }
  html, body {
    width: 1200px; height: 843px; overflow: hidden;
    background: var(--paper);
    font-family: "Carlito", "Calibri", sans-serif;
  }
  .sheet { position: relative; width: 1200px; height: 843px; }
  .crop-marks { position: absolute; inset: 0; }
  .crop-marks line { stroke: var(--crop-line); stroke-width: 1; }

  .card {
    position: absolute; left: 96px; top: 135px;
    width: 1004px; height: 572px;
    background: var(--card-dark);
  }
  .card__brand-panel {
    position: absolute; left: 34px; top: 0;
    width: 448px; height: 572px;
    background: var(--card-light);
  }
  .brand-name {
    position: absolute; left: 0; right: 0; top: 240px;
    display: flex; align-items: center; justify-content: center; gap: 14px;
    color: var(--brand-grey);
    font-size: 66px; font-weight: 400; letter-spacing: 1px;
    line-height: 1;
  }
  .brand-name__dot {
    width: 22px; height: 22px; border-radius: 50%;
    background: var(--brand-grey);
  }
  .website {
    position: absolute; left: 0; right: 0; top: 506px;
    text-align: center; color: var(--brand-grey);
    font-size: 25px;
  }

  .card__details {
    position: absolute; right: 79px; top: 0;
    text-align: right; color: var(--text-light);
  }
  .person { position: absolute; right: 0; top: 72px; white-space: nowrap; }
  .person__name { font-size: 31px; font-weight: 700; line-height: 36px; }
  .person__role { font-size: 29px; font-weight: 400; line-height: 36px; }

  .contact { position: absolute; right: 0; top: 244px; list-style: none; white-space: nowrap; }
  .contact__item {
    display: flex; justify-content: flex-end; align-items: center; gap: 12px;
    font-size: 25px; line-height: 28px;
  }
  .contact__icon { width: 22px; height: 22px; flex: none; }
  .contact__icon * { fill: none; stroke: var(--text-light); stroke-width: 1.6; }

  .address {
    position: absolute; right: 0; top: 427px;
    font-style: normal; font-size: 24px; line-height: 28px; white-space: nowrap;
  }
</style>
</head>
<body>
<div class="sheet">
  <svg class="crop-marks" width="1200" height="843" aria-hidden="true">
    <line x1="85" y1="0" x2="85" y2="72"/><line x1="118" y1="35" x2="118" y2="93"/>
    <line x1="0" y1="83" x2="72" y2="83"/><line x1="35" y1="116" x2="93" y2="116"/>
    <line x1="1116" y1="0" x2="1116" y2="72"/><line x1="1083" y1="35" x2="1083" y2="93"/>
    <line x1="1128" y1="83" x2="1200" y2="83"/><line x1="1107" y1="116" x2="1166" y2="116"/>
    <line x1="35" y1="725" x2="93" y2="725"/><line x1="0" y1="759" x2="72" y2="759"/>
    <line x1="118" y1="749" x2="118" y2="808"/><line x1="85" y1="771" x2="85" y2="843"/>
    <line x1="1107" y1="725" x2="1166" y2="725"/><line x1="1128" y1="759" x2="1200" y2="759"/>
    <line x1="1083" y1="749" x2="1083" y2="808"/><line x1="1116" y1="771" x2="1116" y2="843"/>
  </svg>

  <div class="card">
    <div class="card__brand-panel">
      <div class="brand-name">veranix<span class="brand-name__dot"></span></div>
      <div class="website">www.veranix.ch</div>
    </div>

    <div class="card__details">
      <div class="person">
        <div class="person__name">Marco Lendi</div>
        <div class="person__role">CEO</div>
      </div>

      <ul class="contact">
        <li class="contact__item">
          <svg class="contact__icon" viewBox="0 0 22 22"><rect x="6" y="2" width="10" height="17" rx="1.5" transform="rotate(-20 11 11)"/></svg>
          +41 79 555 0187
        </li>
        <li class="contact__item">
          <svg class="contact__icon" viewBox="0 0 22 22"><path d="M7 3 L4 5 C3 11 8 18 15 19 L18 16 L15 13 L13 15 C10 14 8 11 8 9 L10 7 Z"/></svg>
          +41 71 555 0342
        </li>
        <li class="contact__item">
          <svg class="contact__icon" viewBox="0 0 22 22"><path d="M2 9 L11 3 L20 9 L20 19 L2 19 Z M2 9 L11 15 L20 9 M2 19 L9 13 M20 19 L13 13"/></svg>
          marco.lendi@veranix.ch
        </li>
      </ul>

      <address class="address">
        Veranix GmbH<br>
        Lindenhalde 7<br>
        9247 Talwil<br>
        Switzerland
      </address>
    </div>
  </div>
</div>
</body>
</html>
```